Full re-design of visual identity

We have just re-designed our logo and would like to apply it on our folders, business cards, stationery, and etc... we are attaching new logo + the material we need to re-design... we will provide full corel draw files to help make job easier and also because lot of icons and artwork can be still used...

any doubts we are at your disposal. thanks in advance.

```html
<!DOCTYPE html>
<html lang="en">
<head>
<meta charset="utf-8">
<title>Corvalt Letterhead</title>
<link rel="stylesheet" href="https://fonts.googleapis.com/css2?family=Titillium+Web:wght@400;600;700&display=swap">
<style>
  :root {
    --backdrop: #f1f1f1;
    --paper: #ffffff;
    --ink: #3a3a3a;
    --brand-grey: #8a8a8a;
    --brand-orange: #ee7a37;
    --watermark: #ebebeb;
    --signature-fill: #f3f3f3;
  }
  * { margin: 0; padding: 0; box-sizing: border-box; }
  html, body { width: 1200px; height: 1000px; overflow: hidden; }
  body {
    background: var(--backdrop);
    font-family: "Titillium Web", Arial, sans-serif;
    color: var(--ink);
    position: relative;
  }
  .letterhead {
    position: absolute;
    top: 190px;
    width: 440px;
    height: 615px;
    background: var(--paper);
    overflow: hidden;
  }
  .letterhead--plain { left: 130px; }
  .letterhead--accented { left: 613px; }

  .brand {
    position: absolute;
    top: 26px;
    right: 38px;
    display: flex;
    align-items: center;
    gap: 4px;
  }
  .brand__name {
    font-size: 22px;
    font-weight: 700;
    color: var(--brand-grey);
    letter-spacing: -0.5px;
    line-height: 1;
  }
  .brand__dot {
    width: 12px; height: 12px;
    border-radius: 50%;
    background: var(--brand-orange);
  }

  .watermark {
    position: absolute;
    left: 215px;
    top: 330px;
    width: 220px;
    height: 220px;
    border-radius: 50%;
    background: var(--watermark);
  }

  .letter {
    position: absolute;
    left: 58px;
    top: 160px;
    width: 314px;
    font-size: 8.1px;
    line-height: 10.45px;
  }
  .letter__greeting { margin-bottom: 10px; }
  .letter__body {
    margin-left: 14px;
    text-align: justify;
    hyphens: auto;
  }
  .letter__body + .letter__body { margin-top: 22px; }

  .signature {
    position: absolute;
    left: 262px;
    top: 425px;
    width: 100px;
    height: 30px;
    background: var(--signature-fill);
    border-radius: 3px;
  }

  .contact {
    position: absolute;
    left: 60px;
    width: 330px;
    top: 582px;
    font-size: 6.3px;
    line-height: 9px;
    font-style: normal;
    text-align: center;
  }
  .contact__row { display: flex; justify-content: center; gap: 6px; align-items: center; }
  .contact svg { width: 6px; height: 6px; vertical-align: -1px; margin-right: 1px; }
  .contact svg * { fill: var(--brand-orange); }

  .corner-mark {
    position: absolute;
    left: 392px;
    top: 584px;
    width: 20px; height: 20px;
    border-radius: 50%;
    background: var(--brand-orange);
  }
  .footer-band--grey {
    position: absolute; left: 0; bottom: 0;
    width: 316px; height: 8px;
    background: var(--brand-grey);
  }
  .footer-band--orange {
    position: absolute; right: 0; bottom: 0;
    width: 118px; height: 8px;
    background: var(--brand-orange);
  }
</style>
</head>
<body>

<svg width="0" height="0" style="position:absolute">
  <symbol id="icon-pin" viewBox="0 0 10 10"><path d="M5 0a3.5 3.5 0 0 0-3.5 3.5C1.5 6 5 10 5 10s3.5-4 3.5-6.5A3.5 3.5 0 0 0 5 0zm0 5a1.5 1.5 0 1 1 0-3 1.5 1.5 0 0 1 0 3z"/></symbol>
  <symbol id="icon-phone" viewBox="0 0 10 10"><path d="M2 0l2 2.5-1 1.2a6 6 0 0 0 3.3 3.3l1.2-1L10 8l-1.5 2C4 10 0 6 0 1.5z"/></symbol>
  <symbol id="icon-fax" viewBox="0 0 10 10"><path d="M2 0h5v3H2zM0 3.5h10V10H0z"/></symbol>
  <symbol id="icon-mail" viewBox="0 0 10 10"><path d="M0 2h10v6H0zM0 2l5 3.5L10 2"/></symbol>
  <symbol id="icon-web" viewBox="0 0 10 10"><circle cx="5" cy="5" r="5"/></symbol>
</svg>

<section class="letterhead letterhead--plain">
  <div class="brand"><span class="brand__name">Corvalt</span><span class="brand__dot"></span></div>
  <article class="letter">
    <p class="letter__greeting">Dear Client,</p>
    <p class="letter__body">Lorem ipsum dolor sit amet, consectetur adipiscing elit. Nulla sodales nisi vitae Lorem ipsum dolor sit amet, consectetur adipiscing elit. Suspendisse feugiat eros nisl, a facilisis risus eleifend sed. Aliquam mauris enim, fermentum eu lacinia sit amet, laoreet eu leo. Nullam eleifend nulla in libero tristique, ac vulputate odio tincidunt. Etiam non condimentum tortor. Integer suscipit neque nec odio porttitor cursus. Phasellus a sapien blandit, suscipit justo id, condimentum ante. Morbi tristique justo risus, id mattis dui molestie ut. Nullam volutpat ut quam commodo faucibus. Pellentesque urna est, interdum in elit quis, pharetra elementum orci. Nam pharetra velit molestie justo placerat scelerisque.</p>
    <p class="letter__body">Ut vitae interdum diam, in euismod ante. Pellentesque volutpat, risus sit amet sodales hendrerit, mi turpis vulputate dolor, eget cursus nulla eros nec tellus. Nulla tincidunt molestie libero vel pretium. Donec condimentum nulla sit amet risus semper imperdiet. Duis congue eros nec diam blandit, et pellentesque sapien auctor. Curabitur iaculis enim lectus, in imperdiet mauris mattis eget. Etiam ac ornare metus. Mauris risus leo, egestas at dolor a, ultrices adipiscing est. Nunc faucibus scelerisque mollis. Pellentesque aliquet mauris tellus, id dignissim risus viverra et. Mauris venenatis lobortis eros. Nam id diam in ligula malesuada feugiat. Cras turpis felis, aliquet id mauris elementum, feugiat ultricies nisl.</p>
  </article>
  <div class="signature" role="img" aria-label="Handwritten signature of Paul Merrin"></div>
  <address class="contact">
    <div class="contact__row"><span><svg><use href="#icon-pin"/></svg>48, Harbor Lane, Westfield, 20417, Country</span></div>
    <div class="contact__row">
      <span><svg><use href="#icon-phone"/></svg>555-2087-31</span>
      <span><svg><use href="#icon-fax"/></svg>555-2087-32</span>
      <span><svg><use href="#icon-mail"/></svg>hello@corvalt.com</span>
      <span><svg><use href="#icon-web"/></svg>www.corvalt.com</span>
    </div>
  </address>
  <div class="corner-mark"></div>
  <div class="footer-band--grey"></div>
  <div class="footer-band--orange"></div>
</section>

<section class="letterhead letterhead--accented">
  <div class="watermark"></div>
  <div class="brand"><span class="brand__name">Corvalt</span><span class="brand__dot"></span></div>
  <article class="letter">
    <p class="letter__greeting">Dear Client,</p>
    <p class="letter__body">Lorem ipsum dolor sit amet, consectetur adipiscing elit. Nulla sodales nisi vitae Lorem ipsum dolor sit amet, consectetur adipiscing elit. Suspendisse feugiat eros nisl, a facilisis risus eleifend sed. Aliquam mauris enim, fermentum eu lacinia sit amet, laoreet eu leo. Nullam eleifend nulla in libero tristique, ac vulputate odio tincidunt. Etiam non condimentum tortor. Integer suscipit neque nec odio porttitor cursus. Phasellus a sapien blandit, suscipit justo id, condimentum ante. Morbi tristique justo risus, id mattis dui molestie ut. Nullam volutpat ut quam commodo faucibus. Pellentesque urna est, interdum in elit quis, pharetra elementum orci. Nam pharetra velit molestie justo placerat scelerisque.</p>
    <p class="letter__body">Ut vitae interdum diam, in euismod ante. Pellentesque volutpat, risus sit amet sodales hendrerit, mi turpis vulputate dolor, eget cursus nulla eros nec tellus. Nulla tincidunt molestie libero vel pretium. Donec condimentum nulla sit amet risus semper imperdiet. Duis congue eros nec diam blandit, et pellentesque sapien auctor. Curabitur iaculis enim lectus, in imperdiet mauris mattis eget. Etiam ac ornare metus. Mauris risus leo, egestas at dolor a, ultrices adipiscing est. Nunc faucibus scelerisque mollis. Pellentesque aliquet mauris tellus, id dignissim risus viverra et. Mauris venenatis lobortis eros. Nam id diam in ligula malesuada feugiat. Cras turpis felis, aliquet id mauris elementum, feugiat ultricies nisl.</p>
  </article>
  <div class="signature" role="img" aria-label="Handwritten signature of Paul Merrin"></div>
  <address class="contact">
    <div class="contact__row"><span><svg><use href="#icon-pin"/></svg>48, Harbor Lane, Westfield, 20417, Country</span></div>
    <div class="contact__row">
      <span><svg><use href="#icon-phone"/></svg>555-2087-31</span>
      <span><svg><use href="#icon-fax"/></svg>555-2087-32</span>
      <span><svg><use href="#icon-mail"/></svg>hello@corvalt.com</span>
      <span><svg><use href="#icon-web"/></svg>www.corvalt.com</span>
    </div>
  </address>
  <div class="corner-mark"></div>
  <div class="footer-band--grey"></div>
  <div class="footer-band--orange"></div>
</section>

</body>
</html>
```